Systems and Technology Consultants - Website

Design & Build a website for a new company which operates in the Systems and Technology space for Transportation, Government and Commercial sectors.

Overall design should be minimalist in nature.
Should also have a feed that provides news and event updates on the main page.
Logo has already been awarded and should be incorporated into the site.

We like the overall layout, functionality and simplicity of the below sites. Submitted designs could be similar to or a combination of the aspects on these sites, or perhaps a whole different concept - we are open to new ideas.
Norvique.com
Teblo.it

Update 1 Dated 27 May 2014

All I am moving away from the Teblo.it website and would like it to be more aligned with Norvique.com not only in layout but in functionality. I will be extending the deadline of this design brief for two weeks to incorporate additional requirements and will add addtional funding to the project.

Apologies for not having more information available to provide but with so many submissions its getting confusing.

Thanks Derek

Please note that the brief has been updated and the deadline has been extended.

Important: We will need two language versions of the website, English and Arabic; the website is hosted on HostPelican

Hello All, Thank you for your submissions. We have narrowed it down to the final 6 designers and I just wanted to take a moment and provide a bit of feedback regarding the concepts that we like and the modifications we are looking for. First, let me mention some of the design functions we like. - At the top of the homepage we really like the "region" or "language" tab so that the website can be viewed in both English and Arabic. - We like the homepage to have clear color variation so that the different sections of the homepage are distinct. Additionally, we like the bottom portion of the homepage to be in red. We feel that draws attention to our contact information. Again, we would like the colors to integrate black, gray-scale, red, etc. - Having a search tab at the top of the home page, or integrated into the main image, so that the site is easy to navigate. - We especially like the main image to have the scrolling tabs at the bottom so it is easy to browse the services offered (Consultancy, Solutions Architecture, Masters Systems Integration, Independent Design Review). - In regards to the services offered tab we really like the idea that a few people presented that have the outside of our logo with an icon in the middle of consultancy, solutions, etc., etc. Secondly, as mentioned in our brief we really enjoy the design of norvique site. Specially, we enjoy the strong iconic images they use, the way the tabs at the top scroll easily, and contact us page that generates an email. Lastly, I've included some photos of the concept we have been working on. What we are trying to demonstrate is how our company offers a range of services that are essentially linked together. We provide individual services that when combined present the full service package. We would like this concept to be integrated into the over concept of our website. Please feel free to ask for clarification of any of the above points or contact us if you have any additional questions. We appreciate all of your hard work and are very excited to see the updated designs. Best, Marta Vennick Quelbrant Senior Program Manager marta.vennick@quelbrant-example.com

Industry/Entity Type

Government

Font styles to use
Serif
Sans Serif

Requirements
Must have
• Must work on/adapt to various/mobile devices (responsive)
Must be simple and straightforward
Colors should be in line/matching with logo
2 language versions: English and Arabic (no Thai)
Services should be the first group/row of items after/below the main image
Note: the website will be hosted by hostpelican
Nice to have
• Submit feedback form
What's New section
The banner at the bottom of the site should not be too large; we would like a narrow one more
It would be nice if the header/top banner (with Home, About, etc. tabs) could stay in place as you scroll down (like Norvique and Chatterloop)
We will likely only use one image with a Company slogan on the Home page rather than a carousel of images to rotate through
Should not have
• This is the existing website: http://www.quelbrant-example.org
We do not like the animation, the way the banner icons/titles bounce
Not simple enough, we don't like the functionality or how pages load so slowly
We do not like the logo centered - it should be at the left
The banner and its tabs should not be towards the right, we would like them to be centered, to go all the way across and to be below the logo

```html
<!DOCTYPE html>
<html lang="en">
<head>
<meta charset="utf-8">
<title>Quelbrant — Systems Knowledge Delivered</title>
<link rel="stylesheet" href="https://fonts.googleapis.com/css2?family=Open+Sans:wght@400;600;700&family=Oswald:wght@500;600&display=swap">
<style>
:root{
  --red:#c8202a;
  --red-dark:#a3161f;
  --red-footer:#b3141d;
  --ink:#333333;
  --muted:#777777;
  --line:#dddddd;
  --soft:#f2f2f2;
  --dark:#2a2a2a;
  --white:#ffffff;
  --link-blue:#3d8fd6;
}
*{box-sizing:border-box;margin:0;padding:0}
html,body{width:1200px;height:2456px;overflow:hidden}
body{font-family:"Open Sans",Arial,sans-serif;color:var(--ink);background:var(--white);font-size:14px;line-height:1.55}
.wrap{width:1120px;margin:0 auto;position:relative;height:100%}

/* top bar */
.topbar{height:36px;border-bottom:1px solid var(--line);font-size:13px;color:var(--muted)}
.topbar .wrap{display:flex;justify-content:flex-end;align-items:center;gap:28px}
.topbar span{display:flex;align-items:center;gap:7px}

/* header */
.site-header{height:172px}
.brand{position:absolute;left:40px;top:36px;display:flex;align-items:center;gap:14px}
.brand-mark{width:34px;height:34px;background:var(--red)}
.brand-name{font-weight:700;font-size:38px;color:var(--red);letter-spacing:1px}
.social{position:absolute;right:0;top:22px;display:flex;gap:10px}
.social i{display:block;width:26px;height:26px;border-radius:50%;background:var(--link-blue)}
.main-nav{position:absolute;right:0;top:116px;display:flex;gap:8px}
.main-nav a{font-size:13px;font-weight:600;color:var(--ink);text-decoration:none;padding:7px 20px;text-transform:uppercase;letter-spacing:.5px}
.main-nav a.active{background:var(--red);color:var(--white)}

/* hero */
.hero{height:552px;position:relative;overflow:hidden}
.hero-photo{position:absolute;inset:0;background:linear-gradient(100deg,#d9dde2 0%,#eef0f2 38%,#f6f4ef 60%,#e4e2dc 100%)}
.slogan{position:absolute;right:88px;top:196px;text-align:right}
.slogan .line-1{display:inline-block;background:var(--red);color:var(--white);font-family:"Oswald",sans-serif;font-weight:600;font-size:40px;line-height:1.3;padding:2px 22px;letter-spacing:1px}
.slogan .line-2{display:inline-block;margin-top:6px;background:var(--white);color:var(--ink);font-family:"Oswald",sans-serif;font-weight:600;font-size:40px;line-height:1.3;padding:2px 22px;letter-spacing:1px}

/* services */
.services{height:340px;border-bottom:1px solid var(--line)}
.section-title{font-size:22px;font-weight:400;color:var(--ink)}
.section-title em{font-style:normal;color:var(--red)}
.services .section-title{position:absolute;left:0;top:44px}
.arrows{position:absolute;right:0;top:48px;display:flex;gap:8px}
.arrows svg{width:20px;height:20px}
.service-cards{position:absolute;left:0;top:108px;display:flex;gap:40px}
.card{width:346px;height:176px;border-top:5px solid var(--red);background:var(--white);box-shadow:0 1px 4px rgba(0,0,0,.18);padding:22px 22px 0 22px;display:flex;gap:20px}
.card svg{flex:0 0 70px;width:70px;height:70px}
.card h3{font-size:14px;font-weight:700;text-transform:uppercase;margin-bottom:4px}
.card p{font-size:12.5px;color:var(--muted);line-height:1.5}
.read-more{display:inline-block;margin-top:10px;font-size:12.5px;color:var(--red);text-decoration:none}

/* welcome */
.welcome{height:400px;background:var(--soft);border-bottom:1px solid var(--line)}
.welcome .section-title{position:absolute;left:0;top:64px;font-size:24px}
.welcome-text{position:absolute;left:0;top:116px;width:600px;font-size:13.5px;color:var(--muted)}
.welcome-text p{margin-bottom:18px}
.monitor{position:absolute;left:680px;top:150px;width:400px;height:210px;background:linear-gradient(180deg,#3a3a3a,#222);border-radius:6px;padding:12px}
.monitor-screen{width:100%;height:100%;background:linear-gradient(90deg,#e8ecef,#ffffff)}
.monitor-stand{position:absolute;left:850px;top:360px;width:60px;height:18px;background:#bbbbbb}

/* news + contact */
.news-contact{height:520px}
.news{position:absolute;left:0;top:60px;width:540px}
.form-block{position:absolute;left:700px;top:60px;width:420px}
.news .section-title,.form-block .section-title{border-bottom:1px solid var(--line);padding-bottom:12px;margin-bottom:28px}
.news-item{display:flex;gap:24px;margin-bottom:40px}
.news-thumb{flex:0 0 160px;height:120px;background:linear-gradient(180deg,#b9d3e6 0%,#d5dcc8 55%,#7f9f5a 100%)}
.news-item h4{font-size:13px;font-weight:700;color:var(--red);text-transform:uppercase;margin-bottom:6px}
.news-item p{font-size:12.5px;color:var(--muted);line-height:1.5}
.news-item a{font-size:12.5px;color:var(--ink);text-decoration:none}
.field-row{display:flex;gap:14px;margin-bottom:14px}
.field{flex:1;height:34px;border:1px solid #cccccc;font-size:12.5px;color:#999;padding:7px 10px}
.field.message{height:130px;margin-bottom:14px}
.submit{display:inline-block;background:var(--red);color:var(--white);font-size:12.5px;font-weight:600;padding:8px 44px;text-transform:uppercase}

/* footer */
.site-footer{height:396px;background:var(--red-footer);color:var(--white)}
.foot-col{position:absolute;top:72px;width:220px}
.foot-col h5{font-size:15px;font-weight:600;margin-bottom:18px}
.foot-col ul{list-style:none}
.foot-col li{font-size:13px;padding:9px 0;border-bottom:1px dashed rgba(255,255,255,.45);display:flex;align-items:center;gap:8px}
.foot-col li svg{width:8px;height:10px}
.col-1{left:0}.col-2{left:240px}.col-3{left:500px;width:240px}
.foot-col .note{font-size:12.5px;margin-bottom:10px}
.news-input{width:180px;height:28px;background:var(--white);color:#999;font-size:12px;padding:5px 8px;margin-bottom:10px}
.news-btn{display:inline-block;background:var(--dark);color:var(--white);font-size:12px;font-weight:600;padding:5px 22px;text-transform:uppercase}
.foot-brand{position:absolute;right:40px;top:96px;display:flex;flex-direction:column;align-items:center;gap:22px}
.foot-brand .name-line{display:flex;align-items:center;gap:12px}
.foot-brand .mark{width:28px;height:28px;background:var(--white)}
.foot-brand .name{font-weight:700;font-size:32px;letter-spacing:1px;color:var(--white)}
.foot-brand .social i{display:block;width:26px;height:26px;border-radius:50%;background:rgba(255,255,255,.9)}
.foot-brand .social{position:static;display:flex;gap:10px}

/* bottom bar */
.bottom-bar{height:40px;background:var(--dark);color:#bbbbbb;font-size:12px}
.bottom-bar .wrap{display:flex;justify-content:space-between;align-items:center}
</style>
</head>
<body>

<div class="topbar">
  <div class="wrap">
    <span><svg width="14" height="10" viewBox="0 0 14 10"><rect x=".5" y=".5" width="13" height="9" fill="none" stroke="#777"/><path d="M.5 .5 7 6 13.5 .5" fill="none" stroke="#777"/></svg>office@quelbrant-example.com</span>
    <span><svg width="12" height="12" viewBox="0 0 12 12"><path d="M2 1h3l1 3-2 1a7 7 0 0 0 3 3l1-2 3 1v3c-6 1-10-3-9-9z" fill="#c8202a"/></svg>02-4417-3920</span>
  </div>
</div>

<header class="site-header">
  <div class="wrap">
    <div class="brand"><span class="brand-mark"></span><span class="brand-name">QUELBRANT</span></div>
    <div class="social"><i></i><i></i><i></i></div>
    <nav class="main-nav">
      <a class="active" href="#">Home</a>
      <a href="#">Business Unit</a>
      <a href="#">Services</a>
      <a href="#">About Us</a>
      <a href="#">Locations</a>
      <a href="#">Contact Us</a>
    </nav>
  </div>
</header>

<section class="hero">
  <div class="hero-photo" role="img" aria-label="Engineer in a hard hat in front of a team meeting in a bright office"></div>
  <div class="slogan">
    <div class="line-1">SYSTEMS KNOWLEDGE</div><br>
    <div class="line-2">DELIVERED</div>
  </div>
</section>

<section class="services">
  <div class="wrap">
    <h2 class="section-title">Services <em>Offered</em></h2>
    <div class="arrows">
      <svg viewBox="0 0 20 20"><path d="M13 3 6 10l7 7" fill="none" stroke="#999" stroke-width="3"/></svg>
      <svg viewBox="0 0 20 20"><path d="M7 3l7 7-7 7" fill="none" stroke="#c8202a" stroke-width="3"/></svg>
    </div>
    <div class="service-cards">
      <article class="card">
        <svg viewBox="0 0 70 70"><path d="M14 56 44 26" stroke="#c8202a" stroke-width="7" stroke-linecap="round"/><circle cx="48" cy="22" r="10" fill="none" stroke="#333" stroke-width="6"/><path d="M16 14 56 54" stroke="#333" stroke-width="6" stroke-linecap="round"/></svg>
        <div><h3>Construction</h3><p>Lorem ipsum dolor sit amet, consect etur adipiscing elit. Ut felis ligula sit amet nisl.</p><a class="read-more" href="#">Read more →</a></div>
      </article>
      <article class="card">
        <svg viewBox="0 0 70 70"><circle cx="28" cy="38" r="15" fill="none" stroke="#333" stroke-width="9" stroke-dasharray="6 4"/><circle cx="28" cy="38" r="5" fill="#333"/><circle cx="52" cy="18" r="9" fill="none" stroke="#c8202a" stroke-width="6" stroke-dasharray="4 3"/></svg>
        <div><h3>Engineering</h3><p>Lorem ipsum dolor sit amet, consect etur adipiscing elit. Ut felis ligula sit amet nisl.</p><a class="read-more" href="#">Read more →</a></div>
      </article>
      <article class="card">
        <svg viewBox="0 0 70 70"><rect x="6" y="24" width="22" height="22" fill="#333"/><rect x="30" y="24" width="22" height="22" fill="#c8202a"/><rect x="54" y="30" width="10" height="10" fill="#333"/></svg>
        <div><h3>Consulting</h3><p>Lorem ipsum dolor sit amet, consect etur adipiscing elit. Ut felis ligula sit amet nisl.</p><a class="read-more" href="#">Read more →</a></div>
      </article>
    </div>
  </div>
</section>

<section class="welcome">
  <div class="wrap">
    <h2 class="section-title">Welcome to <em>Quelbrant</em></h2>
    <div class="welcome-text">
      <p>Lorem ipsum dolor sit amet, consectetur adipiscing elit. Phasellus tincid unt tellus leo, sodales vestibulum lorem hendrerit vel. Maecenas ut pre tium tortor sodales vestibulum urna hendrerit vel. Mae cenas ut pretium tortor hendrerit vel. Maece nas ut pretium tortor sodales vestibulum urna hendrerit vel. Maecenas ut pretium.</p>
      <p>Maecenas ut pretium tortor sodales vestibulum urna hendrerit vel. Maece nas ut pretium tortor hendrerit vel. Maecenas ut pretium tortor sodales vestibulum urna hendrerit vel. Maecenas ut pretium tortor.</p>
    </div>
    <div class="monitor"><div class="monitor-screen" role="img" aria-label="Desktop screen showing the engineer photo beside the company name"></div></div>
    <div class="monitor-stand"></div>
  </div>
</section>

<section class="news-contact">
  <div class="wrap">
    <div class="news">
      <h2 class="section-title">What's <em>New?</em></h2>
      <div class="news-item">
        <div class="news-thumb" role="img" aria-label="Engineer on a site overlooking green fields"></div>
        <div><h4>Article title goes here</h4><p>Lorem ipsum dolor sit amet, consectetur adipi scing elit. Phasellus eget leo leo. Sed adipiscing mi orci, vel ultrices turpis mattis a ascing elit dolor ipsum.</p><a href="#">Read More</a></div>
      </div>
      <div class="news-item">
        <div class="news-thumb" role="img" aria-label="Engineer on a site overlooking green fields"></div>
        <div><h4>Article title goes here</h4><p>Lorem ipsum dolor sit amet, consectetur adipi scing elit. Phasellus eget leo leo. Sed adipiscing mi orci, vel ultrices turpis mattis a ascing elit dolor ipsum.</p><a href="#">Read More</a></div>
      </div>
    </div>
    <div class="form-block">
      <h2 class="section-title">Send us <em>a Message</em></h2>
      <div class="field-row"><div class="field">Firstname</div><div class="field">Lastname</div></div>
      <div class="field-row"><div class="field">Phone no.</div><div class="field">Email</div></div>
      <div class="field message">Message...</div>
      <span class="submit">Submit</span>
    </div>
  </div>
</section>

<footer class="site-footer">
  <div class="wrap">
    <div class="foot-col col-1">
      <h5>Who we are</h5>
      <ul>
        <li><svg viewBox="0 0 8 10"><path d="M1 1l5 4-5 4" fill="none" stroke="#fff" stroke-width="2"/></svg>Sublink here</li>
        <li><svg viewBox="0 0 8 10"><path d="M1 1l5 4-5 4" fill="none" stroke="#fff" stroke-width="2"/></svg>Sublink here</li>
        <li><svg viewBox="0 0 8 10"><path d="M1 1l5 4-5 4" fill="none" stroke="#fff" stroke-width="2"/></svg>Sublink here</li>
        <li><svg viewBox="0 0 8 10"><path d="M1 1l5 4-5 4" fill="none" stroke="#fff" stroke-width="2"/></svg>Sublink here</li>
      </ul>
    </div>
    <div class="foot-col col-2">
      <h5>What we offer</h5>
      <ul>
        <li><svg viewBox="0 0 8 10"><path d="M1 1l5 4-5 4" fill="none" stroke="#fff" stroke-width="2"/></svg>Sublink here</li>
        <li><svg viewBox="0 0 8 10"><path d="M1 1l5 4-5 4" fill="none" stroke="#fff" stroke-width="2"/></svg>Sublink here</li>
        <li><svg viewBox="0 0 8 10"><path d="M1 1l5 4-5 4" fill="none" stroke="#fff" stroke-width="2"/></svg>Sublink here</li>
        <li><svg viewBox="0 0 8 10"><path d="M1 1l5 4-5 4" fill="none" stroke="#fff" stroke-width="2"/></svg>Sublink here</li>
      </ul>
    </div>
    <div class="foot-col col-3">
      <h5>Newsletter Signup</h5>
      <p class="note">Subscribe to get updates</p>
      <div class="news-input">Enter address</div>
      <span class="news-btn">Submit</span>
    </div>
    <div class="foot-brand">
      <div class="name-line"><span class="mark"></span><span class="name">QUELBRANT</span></div>
      <div class="social"><i></i><i></i><i></i></div>
    </div>
  </div>
</footer>

<div class="bottom-bar">
  <div class="wrap">
    <span>Copyright © 2014 Quelbrant</span>
    <span>FAQ &nbsp;|&nbsp; Sitemap &nbsp;|&nbsp; Privacy Policy</span>
  </div>
</div>

</body>
</html>
```